Local Roofing/Construction company business needs new biz card design

We need a new business card design, current cards are from the start of this operation and generic at best. We are a local Construction Company (General Contractor) with a majority of our work originating from insurance claims-exterior finish work is the main focus (Roofs-Siding-Gutters etc). Heavily involved with homeowners and the low ball offers they receive from insurance company's after a insurable event takes place. I have attached some of our original logo file(s) below.

```html
<!DOCTYPE html>
<html lang="en">
<head>
<meta charset="utf-8">
<title>Halden Construction – Business Card</title>
<link href="https://fonts.googleapis.com/css2?family=Mulish:wght@500;600;700;800;900&family=Open+Sans:wght@400;600;700&display=swap" rel="stylesheet">
<style>
  :root {
    --page: #e9e7e2;
    --ink-dark: #0e1d1e;
    --brand-green: #4caf67;
    --green-edge: #3d9454;
    --text-light: #f2f4f3;
    --text-dark: #0f2420;
    --rule: #2f5a3f;
  }
  * { box-sizing: border-box; margin: 0; padding: 0; }
  html, body { width: 1200px; height: 900px; overflow: hidden; }
  body {
    background: var(--page);
    position: relative;
    font-family: "Mulish", sans-serif;
  }
  .card {
    position: absolute;
    left: 240px;
    width: 720px;
    height: 412px;
    background: var(--ink-dark);
    overflow: hidden;
    box-shadow: 0 10px 28px rgba(0,0,0,.22);
  }

  /* ---------- Front: hours & tagline ---------- */
  .card--front { top: 26px; }
  .hours {
    position: absolute;
    top: 58px; left: 0; right: 0;
    text-align: center;
    color: var(--text-light);
  }
  .hours__title {
    color: var(--brand-green);
    font-weight: 600;
    font-size: 17px;
    letter-spacing: .5px;
  }
  .hours__times {
    margin-top: 4px;
    font-size: 15px;
    font-weight: 500;
    letter-spacing: .3px;
  }
  .hours__emergency {
    margin-top: 8px;
    color: var(--brand-green);
    font-weight: 700;
    font-size: 21px;
    display: inline-flex;
    align-items: center;
    gap: 10px;
  }
  .hours__emergency svg { width: 22px; height: 22px; }
  .front-brand {
    position: absolute;
    top: 198px; left: 0; right: 0;
    display: flex; justify-content: center; align-items: center; gap: 12px;
  }
  .brand-square {
    width: 34px; height: 34px;
    background: var(--brand-green);
    border-radius: 6px;
  }
  .brand-name {
    color: var(--brand-green);
    font-weight: 800;
    font-size: 28px;
    letter-spacing: 1px;
    text-transform: uppercase;
  }
  .front-rule {
    position: absolute;
    top: 300px; left: 90px; right: 90px;
    height: 1px;
    background: linear-gradient(90deg, transparent, var(--rule) 20%, var(--rule) 80%, transparent);
  }
  .tagline {
    position: absolute;
    top: 324px; left: 0; right: 0;
    text-align: center;
    color: var(--text-light);
    font-weight: 900;
    font-size: 25px;
    letter-spacing: .3px;
  }

  /* ---------- Back: contact details ---------- */
  .card--back { top: 466px; }
  .contact-panel {
    position: absolute;
    top: 0; left: 0; bottom: 0;
    width: 418px;
    background: var(--brand-green);
    border-top-right-radius: 46px;
    box-shadow: 9px 0 0 var(--green-edge);
    padding: 46px 0 0 40px;
    color: var(--text-dark);
    font-family: "Open Sans", sans-serif;
    z-index: 1;
  }
  .person__name { font-weight: 700; font-size: 19px; letter-spacing: .3px; }
  .person__role { font-size: 15px; margin-top: -3px; }
  .contact-list { list-style: none; margin-top: 14px; }
  .contact-list li {
    display: flex; align-items: flex-start; gap: 10px;
    font-size: 15.5px; line-height: 1.35; margin-bottom: 4px;
  }
  .contact-list svg { width: 17px; height: 17px; flex: none; margin-top: 2px; }
  .services { margin-top: 22px; padding-left: 62px; }
  .services__title { font-weight: 600; font-size: 16px; text-transform: uppercase; }
  .services__list { list-style: none; margin-top: 3px; }
  .services__list li {
    display: flex; align-items: center; gap: 9px;
    font-size: 15.5px; line-height: 1.4;
    white-space: nowrap;
  }
  .services__list svg { width: 12px; height: 12px; flex: none; }
  .back-brand {
    position: absolute;
    left: 450px; right: 30px; bottom: 76px;
    text-align: right;
  }
  .back-brand .brand-name {
    display: block;
    font-size: 25px;
    line-height: 1.15;
    letter-spacing: .8px;
  }
</style>
</head>
<body>

<section class="card card--front">
  <div class="hours">
    <p class="hours__title">CONNECT</p>
    <p class="hours__times">Monday - Friday: 8am - 6pm | Saturday - Sunday: By Appointment Only</p>
    <p class="hours__emergency">
      <svg viewBox="0 0 24 24" aria-hidden="true"><path fill="currentColor" d="M6.6 10.8a15 15 0 0 0 6.6 6.6l2.2-2.2a1 1 0 0 1 1-.25 11.4 11.4 0 0 0 3.6.57 1 1 0 0 1 1 1V20a1 1 0 0 1-1 1A17 17 0 0 1 3 4a1 1 0 0 1 1-1h3.5a1 1 0 0 1 1 1c0 1.25.2 2.45.57 3.57a1 1 0 0 1-.25 1z"/></svg>
      Emergency: 555-201-9030
    </p>
  </div>
  <div class="front-brand">
    <span class="brand-square"></span>
    <span class="brand-name">Halden Construction</span>
  </div>
  <div class="front-rule"></div>
  <p class="tagline">You Can Trust Our 30 Years Of Combined Experience</p>
</section>

<section class="card card--back">
  <div class="contact-panel">
    <p class="person__name">EVAN MARLOW</p>
    <p class="person__role">Director</p>
    <ul class="contact-list">
      <li>
        <svg viewBox="0 0 24 24" aria-hidden="true"><path fill="currentColor" d="M6.6 10.8a15 15 0 0 0 6.6 6.6l2.2-2.2a1 1 0 0 1 1-.25 11.4 11.4 0 0 0 3.6.57 1 1 0 0 1 1 1V20a1 1 0 0 1-1 1A17 17 0 0 1 3 4a1 1 0 0 1 1-1h3.5a1 1 0 0 1 1 1c0 1.25.2 2.45.57 3.57a1 1 0 0 1-.25 1z"/></svg>
        555-201-4478
      </li>
      <li>
        <svg viewBox="0 0 24 24" aria-hidden="true"><path fill="currentColor" d="M2 5h20v14H2z"/><path fill="none" stroke="#4caf67" stroke-width="1.8" d="M2 5l10 8 10-8"/></svg>
        evan@haldenbuild.com
      </li>
      <li>
        <svg viewBox="0 0 24 24" aria-hidden="true"><g fill="none" stroke="currentColor" stroke-width="1.8"><circle cx="12" cy="12" r="9.5"/><ellipse cx="12" cy="12" rx="4" ry="9.5"/><path d="M2.5 12h19M4 7h16M4 17h16"/></g></svg>
        www.haldenbuild.com
      </li>
      <li>
        <svg viewBox="0 0 24 24" aria-hidden="true"><path fill="currentColor" d="M12 2a7 7 0 0 0-7 7c0 5 7 13 7 13s7-8 7-13a7 7 0 0 0-7-7zm0 9.5A2.5 2.5 0 1 1 12 6.5a2.5 2.5 0 0 1 0 5z"/></svg>
        <span>42 Cedar Hollow Ln,<br>Brookfield, MO 63000</span>
      </li>
    </ul>
    <div class="services">
      <p class="services__title">Our Services</p>
      <ul class="services__list">
        <li><svg viewBox="0 0 12 12" aria-hidden="true"><path fill="currentColor" d="M6 1 0 6h1.5v5h9V6H12z"/></svg>Residential Roofing</li>
        <li><svg viewBox="0 0 12 12" aria-hidden="true"><path fill="currentColor" d="M6 1 0 6h1.5v5h9V6H12z"/></svg>Commercial Roofing</li>
        <li><svg viewBox="0 0 12 12" aria-hidden="true"><path fill="currentColor" d="M6 1 0 6h1.5v5h9V6H12z"/></svg>Storm Restoration</li>
        <li><svg viewBox="0 0 12 12" aria-hidden="true"><path fill="currentColor" d="M6 1 0 6h1.5v5h9V6H12z"/></svg>Exterior Finishes</li>
      </ul>
    </div>
  </div>
  <div class="back-brand">
    <span class="brand-name">Halden</span>
    <span class="brand-name">Construction</span>
  </div>
</section>

</body>
</html>
```